Now Leasing Banner

Looking for a banner that says the following information approx 4' x 30'

Now Leasing Maplebrook Terrace 925-318-6042

Target Market(s)

Drive by traffic

Industry/Entity Type

Residential property management

Requirements
Must have
• Clear and readable from a distance

```html
<!DOCTYPE html>
<html lang="en">
<head>
<meta charset="utf-8">
<title>Now Leasing Banner</title>
<link href="https://fonts.googleapis.com/css2?family=Poppins:ital,wght@1,800&display=swap" rel="stylesheet">
<style>
  :root {
    --canvas: #777777;
    --navy-deep: #020b4a;
    --navy-mid: #0a2a8f;
    --gold-light: #f3ec9a;
    --gold-mid: #d9b85a;
    --gold-dark: #b8862f;
    --silver-light: #ffffff;
    --silver-dark: #c9c9c9;
    --teal-light: #8fe9e6;
    --teal-mid: #3fc0bd;
    --teal-dark: #2a9c9a;
    --sky-warm: #e8b98a;
    --land-green: #4f7a3a;
  }
  * { margin: 0; padding: 0; box-sizing: border-box; }
  html, body {
    width: 1200px; height: 1200px; overflow: hidden;
    background: var(--canvas);
  }
  .banner {
    position: absolute; left: 0; top: 520px;
    width: 1200px; height: 160px; overflow: hidden;
  }
  .banner-art { position: absolute; inset: 0; }
  .headline {
    position: absolute; left: 106px; top: 22px;
    font-family: "Poppins", sans-serif;
    font-weight: 800; font-style: italic;
    text-transform: uppercase;
    filter: drop-shadow(3px 3px 0 #000) drop-shadow(0 0 4px #000);
  }
  .headline-line { display: block; white-space: nowrap; line-height: 1.05; }
  .headline-top {
    font-size: 45px; letter-spacing: 0.5px;
    background: linear-gradient(180deg, var(--gold-light) 0%, var(--gold-mid) 55%, var(--gold-dark) 100%);
    -webkit-background-clip: text; background-clip: text; color: transparent;
  }
  .headline-bottom { font-size: 50px; margin-top: 2px; }
  .property-word {
    background: linear-gradient(180deg, var(--silver-light) 45%, var(--silver-dark) 100%);
    -webkit-background-clip: text; background-clip: text; color: transparent;
  }
  .phone-number {
    background: linear-gradient(180deg, var(--teal-light) 0%, var(--teal-mid) 50%, var(--teal-dark) 100%);
    -webkit-background-clip: text; background-clip: text; color: transparent;
  }
</style>
</head>
<body>
  <section class="banner">
    <svg class="banner-art" width="1200" height="160" viewBox="0 0 1200 160">
      <defs>
        <radialGradient id="navyField" cx="0.35" cy="0.3" r="0.8">
          <stop offset="0" stop-color="var(--navy-mid)"/>
          <stop offset="1" stop-color="var(--navy-deep)"/>
        </radialGradient>
        <linearGradient id="sceneTones" x1="0" y1="0" x2="0" y2="1">
          <stop offset="0" stop-color="#c9a98e"/>
          <stop offset="0.3" stop-color="var(--sky-warm)"/>
          <stop offset="0.5" stop-color="#6f8a5a"/>
          <stop offset="1" stop-color="var(--land-green)"/>
        </linearGradient>
        <linearGradient id="goldEdge" x1="0" y1="0" x2="0" y2="1">
          <stop offset="0" stop-color="var(--gold-light)"/>
          <stop offset="0.5" stop-color="var(--gold-mid)"/>
          <stop offset="1" stop-color="var(--gold-dark)"/>
        </linearGradient>
      </defs>
      <rect class="navy-field" width="1200" height="160" fill="url(#navyField)"/>
      <path class="gold-edge" d="M902 0 C880 30 872 55 892 90 C908 120 890 145 855 160 L1200 160 L1200 0 Z" fill="url(#goldEdge)"/>
      <path class="property-scene" role="img" aria-label="Aerial view of a residential tower above green parkland at sunset"
            d="M912 0 C890 30 882 55 902 90 C918 120 900 145 866 160 L1200 160 L1200 0 Z" fill="url(#sceneTones)"/>
    </svg>
    <h1 class="headline">
      <span class="headline-line headline-top">Now Leasing Maplebrook</span>
      <span class="headline-line headline-bottom"><span class="property-word">Terrace</span> <span class="phone-number">925-318-6042</span></span>
    </h1>
  </section>
</body>
</html>
```